Corporate Travel Technology Company needs new Business Card design

We need a new business card design to reflect our re-branded company. Our company is called tolvEn (pronounced tolvenn) and we provide Business Intelligence and mobile travel management solutions for the corporate travel industry. Our multinational customers use our solutions to manage large travel budgets and frequent travellers, as well as to save money and reduce risk. We'd like to see designs that use the blue and green palette as well as our corporate logo (attached below). The design should communicate innovation, insight, forward thinking, contemporary, trusted.

Target Market(s)

Large multinational corporates and Travel Agencies.

Industry/Entity Type

Business

Contact Information for Business Card

Rosalind Mercer
Chief Executive
tolvEn
Phone number - +61 (0)2 8134 2907
Email address - rosalind.mercer@tolven-example.com
Mobile number - +61 (0)438 516 702
www.tolven-example.com

Font styles to use
Other font styles liked:
• Please use font as close to corporate logo as possible

Colors
0255a3
0393ce
00a990
33b8a4
33a6d7
3176b5

Requirements
Must have
• Please include the words;
• Mobile Travel Management
• Accelerating Travel Business Insights
• Use corporate logo - although icon can be stylised if needed

```html
<!DOCTYPE html>
<html lang="en">
<head>
<meta charset="utf-8">
<title>tolvEn Business Card</title>
<link rel="stylesheet" href="https://fonts.googleapis.com/css2?family=Open+Sans:wght@400;600&display=swap">
<style>
  :root {
    --backdrop: #e8e5e0;
    --card-white: #fbfbfb;
    --ink: #2b2b2b;
    --slate: #4b6269;
    --sky: #33a6d7;
    --azure: #0393ce;
    --mid-blue: #3176b5;
    --navy: #0255a3;
    --tab-blue: #35b6df;
    --back-top: #1fa4de;
    --back-bottom: #3cbde9;
  }
  * { box-sizing: border-box; margin: 0; padding: 0; }
  html, body {
    width: 1200px;
    height: 892px;
    overflow: hidden;
    background: var(--backdrop);
    font-family: "Open Sans", Arial, sans-serif;
  }
  .canvas {
    position: relative;
    width: 1200px;
    height: 892px;
  }
  .card {
    position: absolute;
    top: 284px;
    width: 530px;
    height: 324px;
    border-radius: 4px;
    overflow: hidden;
    box-shadow: 0 8px 22px rgba(0, 0, 0, 0.18);
  }

  /* Front */
  .card-front {
    left: 50px;
    background: var(--card-white);
  }
  .holder {
    position: absolute;
    left: 34px;
    top: 52px;
  }
  .holder-name {
    font-size: 27px;
    font-weight: 400;
    color: var(--sky);
    line-height: 1.2;
  }
  .holder-title {
    font-size: 15px;
    color: var(--ink);
    margin-top: 4px;
  }
  .brand {
    position: absolute;
    right: 36px;
    top: 30px;
    display: flex;
    align-items: center;
    gap: 10px;
  }
  .brand-name {
    font-size: 56px;
    font-weight: 600;
    color: var(--slate);
    letter-spacing: -1px;
    line-height: 1;
  }
  .brand-mark {
    width: 30px;
    height: 30px;
    border: 4px solid var(--sky);
    border-radius: 50%;
  }
  .divider {
    position: absolute;
    left: 258px;
    top: 124px;
    width: 1px;
    height: 86px;
    background: var(--ink);
  }
  .contacts {
    position: absolute;
    left: 282px;
    top: 132px;
    list-style: none;
  }
  .contacts li {
    display: flex;
    align-items: center;
    gap: 10px;
    font-size: 14.5px;
    color: var(--ink);
    line-height: 24px;
  }
  .contacts svg { flex: none; }
  .band {
    position: absolute;
    left: 0;
    bottom: 0;
    width: 530px;
    height: 74px;
  }
  .website {
    position: absolute;
    left: 268px;
    bottom: 20px;
    font-size: 18px;
    color: #ffffff;
    letter-spacing: 0.3px;
  }

  /* Back */
  .card-back {
    left: 620px;
    background: linear-gradient(160deg, var(--back-top), var(--back-bottom));
  }
  .back-brand {
    position: absolute;
    inset: 0;
    display: flex;
    align-items: center;
    justify-content: center;
    gap: 16px;
  }
  .back-brand-name {
    font-size: 96px;
    font-weight: 600;
    color: #ffffff;
    letter-spacing: -2px;
    line-height: 1;
  }
  .back-brand-mark {
    width: 48px;
    height: 48px;
    border: 6px solid #ffffff;
    border-radius: 50%;
  }
</style>
</head>
<body>
<main class="canvas">
  <section class="card card-front" aria-label="Business card front">
    <div class="holder">
      <p class="holder-name">Rosalind Mercer</p>
      <p class="holder-title">Chief Executive</p>
    </div>

    <div class="brand">
      <span class="brand-name">tolvEn</span>
      <span class="brand-mark" aria-hidden="true"></span>
    </div>

    <div class="divider" aria-hidden="true"></div>

    <ul class="contacts">
      <li>
        <svg width="11" height="11" viewBox="0 0 11 11" aria-hidden="true">
          <rect width="11" height="11" rx="1.5" fill="#33a6d7"/>
          <path d="M3 2.5h1.4l.6 1.6-.8.6a4 4 0 0 0 2.1 2.1l.6-.8 1.6.6V8a.8.8 0 0 1-.8.8A5.8 5.8 0 0 1 2.2 3.3.8.8 0 0 1 3 2.5z" fill="#fff"/>
        </svg>
        +61 (0)2 8134 2907
      </li>
      <li>
        <svg width="11" height="11" viewBox="0 0 11 11" aria-hidden="true">
          <rect width="11" height="11" rx="1.5" fill="#33a6d7"/>
          <rect x="3.6" y="2" width="3.8" height="7" rx="0.7" fill="#fff"/>
          <rect x="4.3" y="3" width="2.4" height="4" fill="#33a6d7"/>
        </svg>
        +61 (0)438 516 702
      </li>
      <li>
        <svg width="11" height="11" viewBox="0 0 11 11" aria-hidden="true">
          <rect width="11" height="11" rx="1.5" fill="#33a6d7"/>
          <rect x="2.2" y="3.2" width="6.6" height="4.6" fill="#fff"/>
          <path d="M2.2 3.2 5.5 5.8 8.8 3.2" fill="none" stroke="#33a6d7" stroke-width="0.8"/>
        </svg>
        rosalind.mercer@tolven-example.com
      </li>
    </ul>

    <svg class="band" viewBox="0 0 530 74" aria-hidden="true">
      <defs>
        <linearGradient id="bandShade" x1="0" y1="0" x2="1" y2="0">
          <stop offset="0" stop-color="#3176b5"/>
          <stop offset="1" stop-color="#0393ce"/>
        </linearGradient>
        <linearGradient id="tabShade" x1="0" y1="0" x2="1" y2="0">
          <stop offset="0" stop-color="#3ec3e6"/>
          <stop offset="1" stop-color="#33a6d7"/>
        </linearGradient>
      </defs>
      <rect x="0" y="0" width="530" height="74" fill="url(#bandShade)"/>
      <path d="M236 16 Q236 8 246 8 H530 V70 H236 Z" fill="url(#tabShade)"/>
      <rect x="0" y="70" width="530" height="4" fill="#0255a3"/>
    </svg>
    <span class="website">www.tolven-example.com</span>
  </section>

  <section class="card card-back" aria-label="Business card back">
    <div class="back-brand">
      <span class="back-brand-mark" aria-hidden="true"></span>
      <span class="back-brand-name">tolvEn</span>
    </div>
  </section>
</main>
</body>
</html>
```